Law Firm Profile

I need a Law firm Profile design. Something professional, corporate inspired, unique and sophisticated. Preferred colours are blue, grey and white. Completion timeline is 5 days. Details of law firm are in the uploaded document

```html
<!DOCTYPE html>
<html lang="en">
<head>
<meta charset="utf-8">
<title>KLV Advocates Law Firm — Firm Profile</title>
<link rel="stylesheet" href="https://fonts.googleapis.com/css2?family=Playfair+Display:wght@700;800;900&family=Montserrat:wght@300;400;600&display=swap">
<style>
:root{
  --backdrop:#a2b4cf;
  --paper:#ffffff;
  --ink:#1c1c1e;
  --body:#3a3a3f;
  --blue:#1f5cf0;
  --blue-light:#4d86ff;
  --grey-panel:#efefef;
  --dark-box:#2f2f31;
  --night:#140c06;
}
*{box-sizing:border-box;margin:0;padding:0}
html,body{width:1200px;height:2441px;overflow:hidden;background:var(--backdrop)}
body{position:relative;font-family:'Montserrat',sans-serif;color:var(--body)}
.page{position:absolute;left:86px;width:1028px;height:726px;background:var(--paper);overflow:hidden;box-shadow:0 12px 30px rgba(40,60,100,.25)}
.page--cover{top:94px;background:var(--night)}
.page--services{top:858px}
.page--people{top:1621px}
.abs{position:absolute}
.photo{position:absolute}
.serif{font-family:'Playfair Display',serif;font-weight:900;line-height:.92;color:var(--ink)}
.blue{color:var(--blue)}
.copy{position:absolute;font-size:11px;line-height:14.7px;letter-spacing:-.25px;color:var(--body)}

/* cover */
.cover-left-photo{left:0;top:0;width:514px;height:726px;background:radial-gradient(ellipse at 62% 45%,#b8560c 0%,#6a2c06 30%,#2a1206 60%,#120904 100%)}
.cover-right-photo{left:514px;top:0;width:514px;height:726px;background:radial-gradient(ellipse at 50% 55%,#7a4a2a 0%,#4a2a18 40%,#22140c 75%,#120a06 100%)}
.cover-title{left:514px;top:56px;width:514px;text-align:center;color:#fff;font-size:68px;line-height:63px;text-shadow:2px 1px 0 #b3171b}
.cover-name{left:44px;top:380px;color:#fff;font-size:43px;line-height:37px}
.contact{left:44px;width:330px;display:flex;gap:14px;color:#fff;font-size:12.5px;line-height:15px;font-weight:400}
.contact svg{flex:0 0 13px;width:13px;height:13px;margin-top:1px}

/* services */
.services-photo{left:306px;top:0;width:414px;height:726px;background:linear-gradient(180deg,#2f6bff 0%,#3b7cff 40%,#1f5cf0 100%)}
.brand-block{left:35px;top:34px;font-size:34px;line-height:30px}
.intro{left:35px;top:107px;width:238px;border-left:2px solid var(--ink);padding-left:12px}
.intro b{font-weight:600;color:var(--ink)}
.svc-title{font-size:23px;line-height:21px}
.rule{display:inline-block;vertical-align:middle;position:relative;width:64px;height:6px;margin-left:4px}
.rule::before{content:"";position:absolute;left:0;top:4px;width:64px;height:2px;background:var(--blue)}
.rule::after{content:"";position:absolute;right:0;top:0;width:24px;height:2px;background:var(--ink)}

/* people */
.court-photo{left:14px;top:15px;width:485px;height:284px;background:linear-gradient(160deg,#6d4424 0%,#3e2616 45%,#1e130b 100%)}
.admin-box{left:30px;top:187px;width:452px;height:164px;background:var(--dark-box);padding:14px 15px}
.admin-box .serif{color:#fff;font-size:24px;line-height:21px}
.admin-copy{position:relative;margin-top:4px;border-left:2px solid var(--blue);padding-left:12px;color:#e9e9ea}
.statue-photo{left:383px;top:351px;width:100px;height:175px;background:radial-gradient(ellipse at 50% 50%,#8a7a5a 0%,#5a4c36 50%,rgba(255,255,255,0) 72%)}
.key-title{left:33px;top:391px;font-size:34px;line-height:31px}
.key-rule{left:33px;top:488px;width:86px;height:3px;background:var(--blue)}
.partner-name{left:33px;top:500px;font-size:34px;line-height:38px}
.assoc-bar{left:547px;top:38px;width:2px;height:58px;background:var(--ink)}
.assoc-title{left:559px;top:38px;font-size:35px;line-height:32px}
.books-photo{left:778px;top:17px;width:83px;height:80px;background:linear-gradient(90deg,#8a5a2e,#c79a5c 40%,#6b4326 70%,#444)}
.mgmt-title{left:547px;top:218px;font-size:24px;line-height:21px}
.values-panel{left:754px;top:205px;width:274px;height:274px;background:var(--grey-panel)}
.values-title{left:775px;top:218px;font-size:24px;line-height:21px;color:var(--blue)}
.gavel-photo{left:525px;top:436px;width:194px;height:92px;background:linear-gradient(180deg,#3a2214,#1c100a)}
.scales-photo{left:528px;top:500px;width:485px;height:213px;background:radial-gradient(ellipse at 45% 40%,#6a4226 0%,#3a2214 45%,#1a0f0a 100%)}
</style>
</head>
<body>

<!-- Spread 1: cover -->
<section class="page page--cover">
  <div class="photo cover-left-photo" role="img" aria-label="Golden statue of Lady Justice holding scales on a dark background"></div>
  <div class="photo cover-right-photo" role="img" aria-label="Antique brass scales of justice on a wooden desk in a law library"></div>
  <h1 class="abs serif cover-title">KLV<br>ADVOCATES<br>LAW FIRM</h1>
  <h2 class="abs serif cover-name">KLV<br>Advocates<br>Law Firm</h2>

  <div class="abs contact" style="top:520px">
    <svg viewBox="0 0 24 24"><path fill="#fff" d="M12 2a7 7 0 0 0-7 7c0 5 7 13 7 13s7-8 7-13a7 7 0 0 0-7-7zm0 9.5A2.5 2.5 0 1 1 12 6.5a2.5 2.5 0 0 1 0 5z"/></svg>
    <span>Plot No. 14, Kafue Crescent,<br>Hillview Park</span>
  </div>
  <div class="abs contact" style="top:564px">
    <svg viewBox="0 0 24 24"><path fill="#fff" d="M3 5h18v14H3zM5 7v6h4a3 3 0 0 0 6 0h4V7z"/></svg>
    <span>10120, Northmead, Lusaka, Zambia</span>
  </div>
  <div class="abs contact" style="top:593px">
    <svg viewBox="0 0 24 24"><path fill="#fff" d="M6.6 10.8a15 15 0 0 0 6.6 6.6l2.2-2.2a1 1 0 0 1 1-.25 11.4 11.4 0 0 0 3.6.57 1 1 0 0 1 1 1V20a1 1 0 0 1-1 1A17 17 0 0 1 3 4a1 1 0 0 1 1-1h3.5a1 1 0 0 1 1 1c0 1.25.2 2.45.57 3.57a1 1 0 0 1-.25 1z"/></svg>
    <span>+260700123456 | +260900234567,<br>+260970345678 | +260760456789</span>
  </div>
  <div class="abs contact" style="top:637px">
    <svg viewBox="0 0 24 24"><path fill="#fff" d="M6.6 10.8a15 15 0 0 0 6.6 6.6l2.2-2.2a1 1 0 0 1 1-.25 11.4 11.4 0 0 0 3.6.57 1 1 0 0 1 1 1V20a1 1 0 0 1-1 1A17 17 0 0 1 3 4a1 1 0 0 1 1-1h3.5a1 1 0 0 1 1 1c0 1.25.2 2.45.57 3.57a1 1 0 0 1-.25 1z"/></svg>
    <span>+260 211000123</span>
  </div>
  <div class="abs contact" style="top:666px">
    <svg viewBox="0 0 24 24"><path fill="#fff" d="M2 5h20v14H2zm2 2v.5l8 5 8-5V7z"/></svg>
    <span>klvadvocates@lawmail.example</span>
  </div>
</section>

<!-- Spread 2: practice areas -->
<section class="page page--services">
  <div class="photo services-photo" role="img" aria-label="Blue-toned statue of Lady Justice holding scales"></div>

  <h2 class="abs serif brand-block">KLV<br><span class="blue">ADVOCATES</span></h2>
  <p class="copy intro">It was founded in <b>2013 by Mr Daniel K Mbewe S.C,</b> the current <b>Director of Public Prosecutions.</b> The firm represents a wide range of clients both local and international and is dedicated to providing the highest quality of services in various areas of the law including.</p>

  <h3 class="abs serif svc-title" style="left:34px;top:242px"><span class="blue">Corporate</span><br>Law<span class="rule"></span></h3>
  <p class="copy" style="left:36px;top:287px;width:252px">We provide comprehensive legal services for corporate clients including in the areas of corporate governance, regulatory compliance, due diligence and risk management advisory. We seamlessly manage the legal aspects of our clients' transactions and ensure that all documentary &amp; contractual requirements are professionally &amp; strategically executed.</p>

  <h3 class="abs serif svc-title" style="left:35px;top:450px"><span class="blue">Commercial</span><br>Law<span class="rule"></span></h3>
  <p class="copy" style="left:37px;top:495px;width:248px">We have vast knowledge and experience in navigating complex commercial legal matters, including contract drafting, negotiations and compliance. We are aligned with the international environment and our lawyers keep up to date on evolving rules of international law and any applicable conflict of laws issues. Our lawyers understand the interplay between the evolving digitalization of the business environment, jurisdictional variances and the legal implications of innovations to the legal environment.</p>

  <h3 class="abs serif svc-title" style="left:747px;top:45px"><span class="blue">Estate &amp;</span><br>Family Law<span class="rule"></span></h3>
  <p class="copy" style="left:747px;top:90px;width:252px">We are well versed in handling estate planning, Wills, Trusts, guardianship, divorce and probate matters to address clients' specific legal needs. Our flexible approach in implementing the full range of established dispute resolution methods at appropriate stages of the transactions and matters speaks to the successful management of even the most complex cases</p>

  <h3 class="abs serif svc-title" style="left:747px;top:234px"><span class="blue">Debt</span> Collection</h3>
  <p class="copy" style="left:747px;top:258px;width:252px">We efficiently handle the recovery process which is crucial for the businesses, financial institutions and individuals we represent, ensuring that disruptions and cost to our clients are mitigated</p>

  <h3 class="abs serif svc-title" style="left:747px;top:351px">Civil &amp; <span class="blue">Criminal<br>Litigation</span></h3>
  <p class="copy" style="left:747px;top:393px;width:256px">We have a notable &amp; well respected track record in the area of litigation &amp; all ancillary processes, we have handled major cases in commercial, criminal, constitutional and other areas of the law. We are committed to ensuring that our work is backed by meticulous legal analysis, structure &amp; sound strategy, ensuring that we draw from the benefits of the integrated and multi-faceted nature of our practice to ensure best results for our clients;</p>

  <h3 class="abs serif svc-title" style="left:747px;top:575px"><span class="blue">Land</span> Law</h3>
  <p class="copy" style="left:749px;top:598px;width:252px">We have handled a wide range of land matters including trespass litigation, encroachment, rectifications and conveyancing and manage a substantial caseload of cases</p>
</section>

<!-- Spread 3: people and values -->
<section class="page page--people">
  <div class="photo court-photo" role="img" aria-label="Wood-panelled courtroom with judge's bench in warm light"></div>
  <div class="abs admin-box">
    <h3 class="serif">Administrative<br>Law</h3>
    <p class="copy admin-copy">We represent a significant number of clients in the area of public law and have handled a large number of judicial review matters regarding immigration and deportation matters, regulatory infringements among others. We are committed to offering comprehensive guidance, clear communication &amp; swift and appropriate response and high quality strategy from the administrative stage, at first instance, and across all stages of the appeal process</p>
  </div>

  <div class="photo statue-photo" role="img" aria-label="Small bronze statue of Lady Justice"></div>
  <h2 class="abs serif key-title">KEY PERSONNEL<br><span class="blue">MANAGING<br>PARTNER</span></h2>
  <div class="abs key-rule"></div>
  <h3 class="abs serif partner-name">Grace Nkandu</h3>
  <p class="copy" style="left:33px;top:540px;width:430px">Grace Nkandu has more than seven years of experience in various areas of the law including commercial law, mining law, construction law, labour law, company law, constitutional law, human rights law, ICT law, administrative law, legislative drafting, civil and criminal litigation and energy law. She studied law at the Central Lakes University, graduated in 2015 and was admitted to the bar in 2016</p>
  <p class="copy" style="left:33px;top:622px;width:440px">Since April 2022 She has sat on the licensing committee of the Power Sector Licensing Authority and is well versed in the matters relating to the energy sector. She is a member of the Press Freedom Network and advocates for digital rights and freedom of expression. She provides legal advisory services to various civil society organizations and undertakes strategic litigation and she holds a postgraduate diploma in legislative drafting and advocates for legislative reform and advancement in various areas of the law.</p>

  <div class="abs assoc-bar"></div>
  <h2 class="abs serif assoc-title">ASSOCIATE<br><span class="blue">Ruth Banda</span></h2>
  <div class="photo books-photo" role="img" aria-label="Stack of old law books with a pen"></div>
  <p class="copy" style="left:547px;top:106px;width:445px">Ruth Banda has over three years of experience in civil litigation, conveyancing, handling corporate and commercial transactions, contract drafting, family law, human rights law, labour disputes, debt recovery as well as administrative law. She studied at Northfield Open University and graduated in 2016 and was admitted to the Bar in 2020. She is a member of the Public Interest Committee of the National Bar Society and has a keen interest in human rights matters.</p>

  <h2 class="abs serif mgmt-title">MANAGEMENT<br>STRUCTURE</h2>
  <p class="copy" style="left:547px;top:275px;width:186px">We have a dedicated team of personnel whose primary goal is to provide the highest quality of service in compliance with all applicable rules of professional conduct. Our support team is friendly, skilled and diverse and work together to ensure that the lawyer-client relationship is seamlessly and properly managed.</p>

  <div class="abs values-panel"></div>
  <h2 class="abs serif values-title">CORE<br>VALUES</h2>
  <p class="copy" style="left:775px;top:275px;width:238px">We take pride in the quality of our legal services in which we incorporate our core values which include integrity, passion, credibility, continuous professional development and excellent client care in the management of our clients' instructions. The firm is regulated by the National Bar Society, and adherence to legal ethics and conduct forms the backbone of our practice and the firm's culture. We also aim to efficiently to harness creative, bespoke and expert solutions to meet every client's particular needs.</p>

  <div class="photo scales-photo" role="img" aria-label="Scales of justice and wooden gavel in a dim law library"></div>
  <div class="photo gavel-photo" role="img" aria-label="Wooden judge's gavel on its block"></div>
</section>

</body>
</html>
```